A layout of a webpage for oil trade platform

I would like to have a desgin of one page webpage (with section scrollling dowin) that woulf present the new product i.e. oil trade platform for wholesale buyers and sellers.
Layout should consist of the sections similar to the given at: https://porada.leczmypol.pl/panel-planowania-spotkan
However oil industy require more colors and more photo stories than here for doctor.
I. I woul imagine at first below menu a slider with brueg information about the product and its advantages with "more" button next to the prict screen of our platform on different displays (PC and mobile).
II. Bellow the slider I would imagine icons correspoing to the advantages of that plaftorm:
1. Purchase/sale process automation 24/7
2. Access to the best deals
3. Electronic offerings and orderings
4. Transaction status monitoring
5. Data and transaction security
II A) (optional):
In near future we would like to prepare a short video presenation. Hence please prepare a place to display that element here.
At the moment alternatvily please prepare a How it works section that would explan the platform operating process
III. Next secion is about benefits for Oil Purchaser
It can be done either by icons of by text and corresponding grahip for while section.
Benefits:
- Access to cheaper oil
- Convenience of online orders
- Possibility to compare prices on the market
- Transaction history
- Order status monitoring
- Seccurity and transparency of purchase
IV. Next seciont is about benefits for Oil Seller
Benefits:
- New sale channel
- Attracting new clients
- More oil sold
- Transaction security
- Possibility to integrate with distribution infrastructure and logistits for more efficient automation.
V. Contact form
VI. Footer
I would need a layout that that will correspond to the very dynamic logo but I would expect also a clean form, smoth and modern. It has to be proffessional layout with more corporate character.
It can use a paralax features if needed.

```html
<!DOCTYPE html>
<html lang="en">
<head>
<meta charset="utf-8">
<title>Oilvanta – Oil Trade Platform</title>
<link href="https://fonts.googleapis.com/css2?family=Open+Sans:wght@400;600;700&family=Roboto:wght@400;500&display=swap" rel="stylesheet">
<style>
:root{
  --orange:#e8452c;
  --orange-2:#f0642c;
  --navy:#16223f;
  --navy-2:#1d2a4a;
  --ink:#222831;
  --muted:#555b66;
  --field:#f6f4f4;
  --field-line:#ebe7e7;
  --light:#f4f4f5;
  --white:#ffffff;
}
*{box-sizing:border-box;margin:0;padding:0}
html,body{width:1200px;height:2817px;overflow:hidden}
body{font-family:"Open Sans",Arial,sans-serif;color:var(--ink);background:var(--white);position:relative}
.section{position:absolute;left:0;width:1200px}
.brand{display:flex;align-items:center;gap:12px;font-family:"Open Sans",Arial,sans-serif;font-weight:700;font-size:24px;letter-spacing:.5px}
.brand-dot{width:36px;height:36px;border-radius:50%;background:var(--orange)}

/* header */
.site-header{top:0;height:94px;background:var(--white)}
.site-header .brand{position:absolute;left:98px;top:29px;color:var(--navy)}
.main-nav{position:absolute;right:96px;top:0;height:94px;display:flex;align-items:center;gap:46px;font-size:14px;font-weight:600;color:#222}
.main-nav .active{color:var(--orange);position:relative}
.main-nav .active::before{content:"";position:absolute;left:50%;top:-16px;width:8px;height:10px;margin-left:-4px;background:var(--orange);border-radius:50% 50% 50% 50%/60% 60% 40% 40%}

/* hero */
.hero{top:94px;height:484px;background:linear-gradient(180deg,#6b4a2c 0%,#a2673a 45%,#d98a3b 70%,#3a2a1e 100%)}
.hero-devices{position:absolute;left:540px;top:40px;width:560px;height:444px;background:linear-gradient(160deg,rgba(30,32,40,.85),rgba(20,22,30,.95));border-radius:8px 8px 0 0}
.hero-copy{position:absolute;left:98px;top:146px;width:560px;color:var(--white)}
.hero-copy h1{font-size:38px;font-weight:700;letter-spacing:.5px;margin-bottom:14px}
.hero-copy p{font-size:13.5px;line-height:22px;width:545px}
.hero-actions{display:flex;gap:10px;margin-top:28px}
.btn-outline,.btn-solid{height:36px;padding:0 14px;display:flex;align-items:center;font-size:12px;font-weight:600;text-transform:uppercase}
.btn-solid{background:var(--white);color:var(--orange);border:1px solid var(--white)}
.btn-outline{border:1px solid var(--white);color:var(--white);font-weight:700}
.hero-arrow{position:absolute;top:232px}
.hero-arrow.prev{left:36px}.hero-arrow.next{right:36px}

/* features */
.features{top:578px;height:239px;display:flex;justify-content:space-between;padding:0 90px}
.feature{width:180px;text-align:center;padding-top:60px}
.feature svg{display:block;margin:0 auto 14px}
.feature p{font-size:15px;line-height:21px;color:#222}

/* video */
.video{top:817px;height:330px;background:radial-gradient(circle at 55% 40%,#4a4f56 0%,#2a2f36 55%,#1b1f25 100%)}
.video-play{position:absolute;left:573px;top:134px;width:56px;height:56px;border-radius:50%;background:#111}
.video-label{position:absolute;left:0;width:100%;top:218px;text-align:center;color:var(--white);font-weight:600;font-size:16px}

/* titles */
.section-title{font-family:"Roboto",Arial,sans-serif;font-weight:400;font-size:24px;text-align:center;text-transform:uppercase;color:#1c1c1c;letter-spacing:.3px}

/* purchaser */
.purchaser{top:1147px;height:408px}
.purchaser .section-title{margin-top:60px}
.benefit-grid{position:absolute;left:100px;top:124px;display:grid;grid-template-columns:338px 358px 300px;row-gap:34px}
.benefit{display:flex;gap:16px;align-items:flex-start}
.benefit-icon{flex:0 0 90px;height:90px;border-radius:50%;background:var(--navy);border:3px solid #c9ccd4;display:flex;align-items:center;justify-content:center}
.benefit h3{font-size:13px;font-weight:700;color:var(--orange);line-height:20px;margin-top:4px}
.benefit p{font-size:12.5px;line-height:21px;color:var(--muted)}

/* seller */
.seller{top:1555px;height:413px;background:var(--light)}
.seller .section-title{margin-top:68px}
.seller-cards{position:absolute;left:100px;top:203px;display:flex;gap:16px}
.seller-card{width:187px;height:135px;border-radius:6px;background:linear-gradient(180deg,#ef5a33 0%,#e33f25 100%);position:relative;color:var(--white);font-weight:700;font-size:13.5px;text-align:center}
.seller-card .diamond{position:absolute;left:50%;top:-48px;width:66px;height:66px;margin-left:-33px;transform:rotate(45deg);background:var(--orange);border:2px solid #fff3;box-shadow:0 0 0 4px rgba(255,255,255,.15)}
.seller-card .diamond svg{transform:rotate(-45deg);position:absolute;left:17px;top:17px}
.seller-card span{position:absolute;left:10px;right:10px;bottom:34px;line-height:20px}

/* contact */
.contact{top:1968px;height:474px}
.contact .section-title{margin-top:62px}
.contact-form{position:absolute;left:272px;top:128px;width:656px;display:grid;grid-template-columns:323px 323px;gap:11px 10px}
.field{height:43px;background:var(--field);border:1px solid var(--field-line);font-size:12px;color:#555;padding:14px 20px}
.field.message{grid-column:1/3;height:112px}
.submit{grid-column:1/3;justify-self:center;width:122px;height:41px;background:var(--orange);color:var(--white);font-size:14px;font-weight:600;display:flex;align-items:center;justify-content:center;margin-top:1px}

/* footer */
.site-footer{top:2442px;height:375px;background:linear-gradient(180deg,var(--navy-2),var(--navy));color:#e6e8ee}
.site-footer .brand{position:absolute;left:98px;top:62px;color:var(--white)}
.footer-contact{position:absolute;left:96px;top:128px;font-size:13px;line-height:21px}
.footer-contact li{list-style:none;display:flex;gap:14px;margin-bottom:13px}
.footer-col{position:absolute;top:50px}
.footer-col h4{font-size:15px;font-weight:600;text-transform:uppercase;color:var(--white);margin-bottom:18px}
.quick-links{left:402px}
.quick-links li{list-style:none;font-size:12.5px;line-height:24px}
.quick-links li::before{content:"»";margin-right:14px}
.social{left:605px}
.social li{list-style:none;display:flex;align-items:center;gap:10px;font-size:14px;margin-bottom:12px}
.social li i{width:27px;height:27px;border:1px solid #e6e8ee;border-radius:50%;display:block}
.signup{left:813px;width:290px}
.signup p{font-size:12px;line-height:21px;margin-bottom:14px}
.signup .field{background:var(--white);height:42px;font-size:11px;padding:13px 14px;color:#666}
.signup .btn-sub{margin-top:10px;width:100px;height:41px;background:var(--orange);color:var(--white);font-size:12px;font-weight:700;display:flex;align-items:center;justify-content:center}
.copyright{position:absolute;left:0;width:100%;top:324px;text-align:center;font-size:12px;color:#e6e8ee}
</style>
</head>
<body>

<header class="section site-header">
  <div class="brand"><span class="brand-dot"></span>Oilvanta</div>
  <nav class="main-nav">
    <span class="active">HOME</span><span>ABOUT US</span><span>ADVANTAGES</span><span>BENEFITS</span><span>CONTACT US</span>
  </nav>
</header>

<section class="section hero" role="img" aria-label="Oil pump jack silhouetted against a sunset sky">
  <div class="hero-devices" role="img" aria-label="Platform dashboard shown on a desktop monitor, laptop, tablet and phone"></div>
  <div class="hero-copy">
    <h1>WELCOME TO OILVANTA</h1>
    <p>Contrary to popular belief, Lorem Ipsum is not simply random text. It has roots in a piece of classical Latin literature from 45 BC, making it over 2000 years old. a Latin professor at Hampden-Sydney College.</p>
    <div class="hero-actions"><span class="btn-solid">Read more</span><span class="btn-outline">Contact us</span></div>
  </div>
  <svg class="hero-arrow prev" width="12" height="20" viewBox="0 0 12 20"><path d="M10 2 2 10l8 8" fill="none" stroke="#fff" stroke-width="2.5"/></svg>
  <svg class="hero-arrow next" width="12" height="20" viewBox="0 0 12 20"><path d="M2 2l8 8-8 8" fill="none" stroke="#fff" stroke-width="2.5"/></svg>
</section>

<section class="section features">
  <div class="feature">
    <svg width="60" height="60" viewBox="0 0 60 60"><path d="M30 6a24 24 0 1 1-21 12" fill="none" stroke="#e8452c" stroke-width="3" stroke-dasharray="5 3"/><path d="M4 14l5 5 5-6" fill="none" stroke="#e8452c" stroke-width="3"/><text x="30" y="37" text-anchor="middle" font-family="Open Sans,sans-serif" font-weight="700" font-size="18" fill="#e8452c">24</text></svg>
    <p>Purchase/sale process automation 24/7</p>
  </div>
  <div class="feature">
    <svg width="60" height="60" viewBox="0 0 60 60"><circle cx="22" cy="12" r="6" fill="#e8452c"/><circle cx="40" cy="12" r="6" fill="#e8452c"/><path d="M14 22h14l4 10h-6v20h-8V32h-4zM46 22H34l-4 10h6v20h8V32h4z" fill="#e8452c"/></svg>
    <p>Access to the best deals</p>
  </div>
  <div class="feature">
    <svg width="60" height="60" viewBox="0 0 60 60"><path d="M34 6h18v18L26 50 10 34z" fill="#e8452c"/><circle cx="44" cy="14" r="3.5" fill="#fff"/></svg>
    <p>Electronic offerings and orderings</p>
  </div>
  <div class="feature">
    <svg width="60" height="60" viewBox="0 0 60 60"><rect x="10" y="10" width="40" height="28" rx="3" fill="none" stroke="#e8452c" stroke-width="3"/><path d="M10 18h40" stroke="#e8452c" stroke-width="4"/><rect x="4" y="24" width="36" height="26" rx="3" fill="#fff" stroke="#e8452c" stroke-width="3"/><path d="M10 36h14M10 42h20" stroke="#e8452c" stroke-width="3"/></svg>
    <p>Transaction status monitoring</p>
  </div>
  <div class="feature">
    <svg width="60" height="60" viewBox="0 0 60 60"><path d="M20 26v-8a10 10 0 0 1 20 0v8" fill="none" stroke="#e8452c" stroke-width="4"/><rect x="14" y="26" width="32" height="28" rx="3" fill="#e8452c"/><circle cx="30" cy="38" r="3" fill="#fff"/><path d="M30 40v6" stroke="#fff" stroke-width="3"/></svg>
    <p>Data and transaction security</p>
  </div>
</section>

<section class="section video" role="img" aria-label="Oil field worker in a hard hat at an industrial site">
  <div class="video-play"><svg width="56" height="56" viewBox="0 0 56 56"><path d="M22 17l18 11-18 11z" fill="#fff"/></svg></div>
  <div class="video-label">Video Presentation</div>
</section>

<section class="section purchaser">
  <h2 class="section-title">Benefits for oil purchaser</h2>
  <div class="benefit-grid">
    <div class="benefit"><div class="benefit-icon"><svg width="36" height="36" viewBox="0 0 36 36"><rect x="8" y="6" width="20" height="26" rx="2" fill="none" stroke="#fff" stroke-width="2"/><path d="M18 13c3 4 4 6 4 8a4 4 0 0 1-8 0c0-2 1-4 4-8z" fill="#fff"/></svg></div><div><h3>Access to cheaper oil</h3><p>Lorem Ipsum is simply dummy text<br>the prin typesetting industry.</p></div></div>
    <div class="benefit"><div class="benefit-icon"><svg width="36" height="36" viewBox="0 0 36 36"><rect x="5" y="7" width="26" height="18" rx="1" fill="none" stroke="#fff" stroke-width="2"/><path d="M13 31h10M18 25v6M12 18l6-6M17 19l5-5" stroke="#fff" stroke-width="2"/></svg></div><div><h3>Convenience of online orders</h3><p>Lorem Ipsum is simply dummy text<br>the prin typesetting industry.</p></div></div>
    <div class="benefit"><div class="benefit-icon"><svg width="36" height="36" viewBox="0 0 36 36"><path d="M10 10h16v22H10z" fill="none" stroke="#fff" stroke-width="2"/><path d="M14 10V6h8v4" stroke="#fff" stroke-width="2" fill="none"/><text x="18" y="26" text-anchor="middle" fill="#fff" font-size="10" font-family="Open Sans,sans-serif" font-weight="700">%</text></svg></div><div><h3>Possibility to compare prices<br>on the market</h3><p>Lorem Ipsum is simply dummy text<br>the prin typesetting industry.</p></div></div>
    <div class="benefit"><div class="benefit-icon"><svg width="36" height="36" viewBox="0 0 36 36"><circle cx="18" cy="18" r="12" fill="none" stroke="#fff" stroke-width="2" stroke-dasharray="6 3"/><path d="M18 11v7l5 3" stroke="#fff" stroke-width="2" fill="none"/></svg></div><div><h3>Transaction history</h3><p>Lorem Ipsum is simply dummy text<br>the prin typesetting industry.</p></div></div>
    <div class="benefit"><div class="benefit-icon"><svg width="36" height="36" viewBox="0 0 36 36"><rect x="5" y="7" width="26" height="18" rx="1" fill="none" stroke="#fff" stroke-width="2"/><path d="M13 31h10M18 25v6" stroke="#fff" stroke-width="2"/><circle cx="13" cy="16" r="1.5" fill="#fff"/><circle cx="18" cy="16" r="1.5" fill="#fff"/><circle cx="23" cy="16" r="1.5" fill="#fff"/></svg></div><div><h3>Order status monitoring</h3><p>Lorem Ipsum is simply dummy text<br>the prin typesetting industry.</p></div></div>
    <div class="benefit"><div class="benefit-icon"><svg width="36" height="36" viewBox="0 0 36 36"><path d="M12 16v-4a6 6 0 0 1 12 0v4" fill="none" stroke="#fff" stroke-width="2"/><rect x="9" y="16" width="18" height="15" rx="2" fill="none" stroke="#fff" stroke-width="2"/><circle cx="18" cy="23" r="2" fill="#fff"/></svg></div><div><h3>Security and transparency of<br>purchase</h3><p>Lorem Ipsum is simply dummy text<br>the prin typesetting industry.</p></div></div>
  </div>
</section>

<section class="section seller">
  <h2 class="section-title">Benefits for oil seller</h2>
  <div class="seller-cards">
    <div class="seller-card"><div class="diamond"><svg width="32" height="32" viewBox="0 0 32 32"><circle cx="16" cy="16" r="11" fill="none" stroke="#fff" stroke-width="2"/><text x="16" y="20" text-anchor="middle" fill="#fff" font-size="11" font-family="Open Sans,sans-serif" font-weight="700">%</text></svg></div><span>New sale channel</span></div>
    <div class="seller-card"><div class="diamond"><svg width="32" height="32" viewBox="0 0 32 32"><path d="M8 10l1 2 2 .3-1.5 1.4.4 2L8 14.7 6.1 15.7l.4-2L5 12.3 7 12zM16 8l1 2 2 .3-1.5 1.4.4 2-1.9-1-1.9 1 .4-2L13 10.3l2-.3zM24 10l1 2 2 .3-1.5 1.4.4 2-1.9-1-1.9 1 .4-2-1.5-1.4 2-.3z" fill="#fff"/><rect x="5" y="20" width="22" height="6" fill="#fff"/></svg></div><span>Attracting new clients</span></div>
    <div class="seller-card"><div class="diamond"><svg width="32" height="32" viewBox="0 0 32 32"><path d="M16 4c3 4 5 7 5 9a5 5 0 0 1-10 0c0-2 2-5 5-9z" fill="#fff"/><path d="M4 24c4-3 8-3 12 0h8c2 0 2 3 0 3H10" fill="none" stroke="#fff" stroke-width="2"/></svg></div><span>More oil sold</span></div>
    <div class="seller-card"><div class="diamond"><svg width="32" height="32" viewBox="0 0 32 32"><path d="M16 3l11 4v8c0 7-5 12-11 14C10 27 5 22 5 15V7z" fill="none" stroke="#fff" stroke-width="2"/><text x="16" y="21" text-anchor="middle" fill="#fff" font-size="12" font-family="Open Sans,sans-serif" font-weight="700">$</text></svg></div><span>Transaction security</span></div>
    <div class="seller-card"><div class="diamond"><svg width="32" height="32" viewBox="0 0 32 32"><circle cx="16" cy="16" r="6" fill="none" stroke="#fff" stroke-width="2"/><circle cx="16" cy="16" r="11" fill="none" stroke="#fff" stroke-width="3" stroke-dasharray="3 3"/></svg></div><span>Possibility to integrate<br>with distribution<br>»</span></div>
  </div>
</section>

<section class="section contact">
  <h2 class="section-title">Contact form</h2>
  <form class="contact-form">
    <div class="field">First Name</div>
    <div class="field">Last Name</div>
    <div class="field">Email Address</div>
    <div class="field">Phone</div>
    <div class="field message">Message</div>
    <div class="submit">SUBMIT</div>
  </form>
</section>

<footer class="section site-footer">
  <div class="brand"><span class="brand-dot"></span>Oilvanta</div>
  <ul class="footer-contact">
    <li><svg width="16" height="20" viewBox="0 0 16 20"><path d="M8 1a6 6 0 0 1 6 6c0 5-6 12-6 12S2 12 2 7a6 6 0 0 1 6-6z" fill="none" stroke="#e6e8ee" stroke-width="1.6"/><circle cx="8" cy="7" r="2" fill="#e6e8ee"/></svg><span>12 Refinery Lane, Harbor District<br>Northport</span></li>
    <li><svg width="16" height="18" viewBox="0 0 16 18"><path d="M3 2l3 0 1 4-2 1c1 3 3 5 5 6l1-2 4 1v3c0 1-1 2-2 2C6 16 1 10 1 4c0-1 1-2 2-2z" fill="none" stroke="#e6e8ee" stroke-width="1.5"/></svg><span>Phone : (555) 0142 7781</span></li>
    <li><svg width="16" height="18" viewBox="0 0 16 18"><rect x="1" y="4" width="14" height="10" fill="none" stroke="#e6e8ee" stroke-width="1.5"/><path d="M1 4l7 6 7-6" fill="none" stroke="#e6e8ee" stroke-width="1.5"/></svg><span>hello@oilvanta-trade.com</span></li>
  </ul>
  <div class="footer-col quick-links">
    <h4>Quick links</h4>
    <ul><li>Home</li><li>About Us</li><li>Advantages</li><li>Benefits</li><li>Form</li><li>Contact Us</li></ul>
  </div>
  <div class="footer-col social">
    <h4>Social media</h4>
    <ul><li><i></i>Friendwall</li><li><i></i>Chirpline</li><li><i></i>Circleplus</li><li><i></i>Streamtube</li></ul>
  </div>
  <div class="footer-col signup">
    <h4>Sign up to receive email</h4>
    <p>Excepteur sint occaecat cupidatat non proident, sunt in culpa qui Nemo enim ipsam voluptatem</p>
    <div class="field">Enter Name</div>
    <div class="btn-sub">SUBSCRIBE</div>
  </div>
  <div class="copyright">Copyright © Oilvanta 2017. All rights reserved.</div>
</footer>

</body>
</html>
```